Lanternfield Drinks business cards

We need a business card design for our new logo. The company is modern, progressive, professional, yet approachable. The key products are ready to drink bottles and cans of coffee based beverages.
These cards will be a critical part of the first impression made by our sales organization, business development team, and all external facing personnel.
Card can be a vertical or horizontal orientation.

Target Market(s)

Customers, suppliers, business partners

Industry/Entity Type

Business

Contact Information for Business Card

Business cards should feature Company Name and Logo.

Font styles to use
Serif

Colors

Designer to choose colors to be used in the design.

Requirements
Must have
• Strong readability of Name, phone #, mobile number and email address.
• Job title, website url, Street Address, and other details can be secondary level readability.
Nice to have
• High impact, simplistic quality design.
• Ok to utilize the 'H in the box' separate from the company name

```html
<!DOCTYPE html>
<html lang="en">
<head>
<meta charset="utf-8">
<title>Lanternfield Drinks business cards</title>
<link rel="stylesheet" href="https://fonts.googleapis.com/css2?family=Crimson+Pro:ital,wght@0,400;0,600;0,700;1,400&display=swap">
<style>
  :root {
    --backdrop: #c6c6c6;
    --orange-top: #dd8634;
    --orange-bottom: #bf4a2a;
    --brand-red: #c94a2a;
    --card-white: #f3f3f3;
    --ink: #222222;
    --rule: #d99a5a;
    --on-orange: #ffffff;
  }
  * { margin: 0; padding: 0; box-sizing: border-box; }
  html, body {
    width: 1200px; height: 576px; overflow: hidden;
    background: var(--backdrop);
    font-family: "Crimson Pro", Georgia, serif;
  }
  .stage { position: relative; width: 1200px; height: 576px; }
  .card {
    position: absolute; top: 138px; width: 484px; height: 294px;
    border-radius: 14px; overflow: hidden;
  }
  .card--front {
    left: 82px;
    background: linear-gradient(180deg, var(--orange-top), var(--orange-bottom));
  }
  .card--back { left: 600px; background: var(--card-white); }

  .brand { position: absolute; display: flex; flex-direction: column; align-items: center; }
  .brand__square { border: 3px solid currentColor; }
  .brand__name {
    font-weight: 600; text-transform: uppercase; letter-spacing: 0.04em;
    white-space: nowrap; line-height: 1;
  }
  .card--front .brand {
    left: 0; right: 0; top: 106px; color: var(--on-orange);
  }
  .card--front .brand__square { width: 54px; height: 54px; margin-bottom: 18px; }
  .card--front .brand__name { font-size: 30px; }

  .card--back .brand {
    left: 18px; width: 232px; top: 110px; color: var(--brand-red);
  }
  .card--back .brand__square { width: 40px; height: 40px; margin-bottom: 14px; }
  .card--back .brand__name { font-size: 21px; }

  .divider {
    position: absolute; left: 254px; top: 58px; width: 1px; height: 172px;
    background: var(--rule);
  }
  .contact { position: absolute; left: 277px; top: 62px; color: var(--ink); }
  .contact__name { font-size: 19px; font-weight: 600; color: var(--brand-red); line-height: 1.1; }
  .contact__role { font-size: 12.5px; font-style: italic; margin-top: 3px; }
  .contact__address { font-size: 13.5px; line-height: 17px; margin-top: 22px; }
  .contact__list { list-style: none; margin-top: 4px; font-size: 13.5px; line-height: 17px; }
  .contact__list li { display: flex; align-items: center; gap: 10px; }
  .contact__list svg { width: 10px; height: 10px; fill: var(--brand-red); flex: none; }
</style>
</head>
<body>
<main class="stage">
  <section class="card card--front" aria-label="Card front">
    <div class="brand">
      <div class="brand__square"></div>
      <div class="brand__name">Lanternfield Drinks</div>
    </div>
  </section>

  <section class="card card--back" aria-label="Card back">
    <div class="brand">
      <div class="brand__square"></div>
      <div class="brand__name">Lanternfield Drinks</div>
    </div>
    <div class="divider"></div>
    <div class="contact">
      <div class="contact__name">John Doe Smith</div>
      <div class="contact__role">Managing Director</div>
      <div class="contact__address">234 Anywhere St.,<br>Any Town, US 123456</div>
      <ul class="contact__list">
        <li><svg viewBox="0 0 10 10" aria-hidden="true"><path d="M1 3c0-1 1-2 2-2h4c1 0 2 1 2 2v1H7V3H3v1H1z M2 5h6l1 4H1z"/></svg>555.555.5555</li>
        <li><svg viewBox="0 0 10 10" aria-hidden="true"><path d="M2.5 0h5a1 1 0 0 1 1 1v8a1 1 0 0 1-1 1h-5a1 1 0 0 1-1-1V1a1 1 0 0 1 1-1zM3 1.5v6h4v-6z"/></svg>666.666.7777</li>
        <li><svg viewBox="0 0 10 10" aria-hidden="true"><path d="M0 2h10v6H0z M0.6 2.4 5 5.6 9.4 2.4" stroke="#fff" stroke-width="0.8"/></svg>johndoe@yourwebsite.com</li>
        <li><svg viewBox="0 0 10 10" aria-hidden="true"><circle cx="5" cy="5" r="4.6"/><path d="M0.5 5h9M5 0.5c-2.5 2.5-2.5 6.5 0 9M5 0.5c2.5 2.5 2.5 6.5 0 9" stroke="#fff" stroke-width="0.7" fill="none"/></svg>www.yourwebsite.com</li>
      </ul>
    </div>
  </section>
</main>
</body>
</html>
```